Business Card Design

New business card design

Target Market(s)

Residential & Commercial Property Managers

Industry/Entity Type

Plumbing Services

Contact Information for Business Card

Name - Rowan Keddle, title - Director, Phone Number - 0431 286 517, email - rowan@tbk-plumbing.com.au, Company ABN - 73 215 904 386,

Font styles to use
Sans Serif

Colors
0054AA
0677BA
7BADD7
CADEEF
E8F1F8

```html
<!DOCTYPE html>
<html lang="en">
<head>
<meta charset="utf-8">
<title>TBK Plumbing Services – Business Cards</title>
<link rel="stylesheet" href="https://fonts.googleapis.com/css2?family=Montserrat:wght@300;400;500;600&display=swap">
<style>
  :root {
    --bg: #2b2e33;
    --card-white: #ffffff;
    --ink: #1f2328;
    --band: #1e252c;
    --blue: #2196d6;
    --blue-light: #2aa9e2;
    --blue-deep: #1f8fcf;
    --muted: #55606b;
  }
  * { margin: 0; padding: 0; box-sizing: border-box; }
  html, body { width: 1200px; height: 900px; overflow: hidden; }
  body {
    background: var(--bg);
    font-family: "Montserrat", sans-serif;
    display: flex;
    align-items: center;
    justify-content: center;
    gap: 44px;
  }
  .card {
    position: relative;
    width: 520px;
    height: 298px;
    border-radius: 22px;
    overflow: hidden;
  }
  .card-front { background: var(--card-white); }
  .card-back {
    background: linear-gradient(160deg, var(--blue-light), var(--blue-deep));
    display: flex;
    align-items: center;
    justify-content: center;
  }
  .front-band { position: absolute; inset: 0; width: 100%; height: 100%; }
  .brand-name {
    font-weight: 300;
    letter-spacing: 0.06em;
    white-space: nowrap;
  }
  .card-front .brand-name {
    position: absolute;
    top: 40px;
    left: 0;
    right: 0;
    text-align: center;
    font-size: 26px;
    color: var(--ink);
  }
  .card-back .brand-name {
    font-size: 34px;
    color: var(--card-white);
  }
  .person {
    position: absolute;
    top: 128px;
    left: 34px;
    width: 180px;
    text-align: right;
  }
  .person-name {
    font-size: 20px;
    font-weight: 600;
    color: var(--blue);
  }
  .person-title {
    font-size: 13px;
    font-weight: 400;
    color: var(--ink);
    margin-top: 2px;
  }
  .divider {
    position: absolute;
    top: 118px;
    left: 232px;
    width: 1px;
    height: 74px;
    background: var(--blue);
    opacity: 0.6;
  }
  .contact-list {
    position: absolute;
    top: 116px;
    left: 248px;
    list-style: none;
    font-size: 14px;
    color: var(--ink);
    line-height: 26px;
  }
  .contact-list li { display: flex; align-items: center; gap: 7px; }
  .contact-label { color: var(--blue); }
  .contact-icon { width: 11px; height: 11px; flex: none; }
</style>
</head>
<body>

  <section class="card card-front" aria-label="Business card front">
    <svg class="front-band" viewBox="0 0 520 298" preserveAspectRatio="none" aria-hidden="true">
      <path d="M0 188 C 150 222, 330 262, 470 298 L0 298 Z" fill="var(--band)"/>
      <path d="M0 176 C 150 212, 330 254, 478 298" fill="none" stroke="var(--blue)" stroke-width="2.5"/>
    </svg>

    <div class="brand-name">TBK Plumbing Services</div>

    <div class="person">
      <div class="person-name">Rowan Keddle</div>
      <div class="person-title">Director</div>
    </div>

    <div class="divider"></div>

    <ul class="contact-list">
      <li><span class="contact-label">ABN</span> - 73 215 904 386</li>
      <li>
        <svg class="contact-icon" viewBox="0 0 12 12" aria-hidden="true">
          <circle cx="6" cy="6" r="6" fill="var(--blue)"/>
          <path d="M4 3.2 L5 3 L5.6 4.6 L4.9 5.2 C5.3 6 6 6.7 6.8 7.1 L7.4 6.4 L9 7 L8.8 8 C6.3 8.4 3.6 5.7 4 3.2 Z" fill="#fff"/>
        </svg>
        0431 286 517
      </li>
      <li>
        <svg class="contact-icon" viewBox="0 0 12 12" aria-hidden="true">
          <rect width="12" height="12" rx="2" fill="var(--blue)"/>
          <path d="M2.5 4 H9.5 V8.5 H2.5 Z M2.5 4 L6 6.6 L9.5 4" fill="none" stroke="#fff" stroke-width="0.9"/>
        </svg>
        rowan@tbk-plumbing.com.au
      </li>
    </ul>
  </section>

  <section class="card card-back" aria-label="Business card back">
    <div class="brand-name">TBK Plumbing Services</div>
  </section>

</body>
</html>
```